Very new and innovative Web design for Property managers of Vacation rentals

We are looking for a new website design for travel agencies and property managers specialised on vacation rentals business, holiday villas and apartments.

The end users of this website are travellers who are looking for a vacation home for their next holiday: this is the reason why the website must be easy to use, attractive, professional, possibly elegant and focused on get new reservations.

This is a draft of our current website: https://intro3.kelumsito.com/
Please consider that we would like to have proposals with a totally different and innovative layout, surprise us!

These are the pages of the website:
• Homepage: feel free to redesign all the homepage as you wish, surprise us with something very new! Please consider that Property manager/Travel agencies usually want to have the opportunity to put in evidence groups of houses with specific characteristics (eg. villas with private swimming pool, apartment in big/small towns, villas with air co, etc…), destinations and tourist areas, and sometimes experiences or activities (please consider that the website layout must be suitable even if some of the previous sections are not used).
• Search page: we’d like to organise the results of the search page in three different ways:
o Grid
o Map
o List
• Property page: to illustrate the characteristics, descriptions, images, …. of the property. It is very important to put in evidence images of the property and to maintain the booking form (and the other call to action bottom – eg. whatsapp) always visible
• Custom pages: static pages composed usually by text, images and call to actions
• Contact us (general form)
• Info request (specific of a property form)
• Booking process
• Blog, organised in four pages:
o Home Page – introduction to the blog
o List of articles
o Single article
o Site Map (presentation of categories and sub-categories)

If possible, we’d prefer to receive the material in Adobe XD or similar so that we can obtain the three versions:
- smartphone
- tablet
- desktop

The website will be then developed in Bootstrap: as a result we’ll need the icons in SVG format (or the library used)

In attachment you can find the map of the website pages

```html
<!DOCTYPE html>
<html lang="en">
<head>
<meta charset="utf-8">
<title>Contact Us – StayLuce</title>
<link rel="stylesheet" href="https://fonts.googleapis.com/css2?family=Mulish:wght@300;400;600;700&family=Prata&family=Cinzel:wght@600&display=swap">
<style>
:root{
  --green:#13b584;
  --ink:#1f1f1f;
  --text:#3a3a3a;
  --muted:#6b6b6b;
  --line:#cfcfcf;
  --footer:#1d1d1d;
  --footer-text:#c9c9c9;
  --white:#ffffff;
}
*{box-sizing:border-box;margin:0;padding:0}
html,body{width:772px;height:1200px;overflow:hidden;background:var(--white)}
body{position:relative;font-family:"Mulish",sans-serif;color:var(--text)}
a{color:inherit;text-decoration:none}
.abs{position:absolute}

/* header */
.site-header{position:absolute;left:0;top:0;width:772px;height:59px;background:var(--white)}
.brand{position:absolute;left:72px;top:20px;display:flex;align-items:center;gap:6px;font-size:18px;font-weight:400;color:var(--ink)}
.brand-dot{width:12px;height:12px;border-radius:50%;background:var(--green)}
.utility-bar{position:absolute;right:0;top:0;width:252px;height:27px;background:var(--green);clip-path:polygon(0 0,100% 0,100% 100%,27px 100%);display:flex;align-items:center;justify-content:flex-end;gap:16px;padding-right:20px;color:var(--white);font-size:7.5px;font-weight:700;letter-spacing:.2px}
.utility-bar span{display:flex;align-items:center;gap:4px}
.main-nav{position:absolute;top:40px;left:366px;display:flex;gap:0;font-size:8.8px;color:var(--ink)}
.main-nav a{margin-right:35px}
.main-nav a.active{color:var(--green);font-weight:600;margin-right:0}

/* hero */
.hero{position:absolute;left:0;top:59px;width:772px;height:184px;background:linear-gradient(90deg,#2e3a2c 0%,#5a5046 30%,#7a6a5a 50%,#4d4a44 70%,#2f3a2e 100%)}
.hero h1{position:absolute;left:0;right:0;top:74px;text-align:center;font-family:"Cinzel",serif;font-weight:600;font-size:30px;color:var(--white);letter-spacing:.5px}

/* content */
.breadcrumb{left:72px;top:264px;font-size:7.8px;color:var(--muted)}
.breadcrumb b{font-weight:400;color:var(--ink)}
.page-title{left:72px;top:297px;font-family:"Prata",serif;font-size:28px;font-weight:400;color:var(--ink)}
.page-intro{left:72px;top:333px;width:424px;font-size:8.8px;line-height:14.6px;font-weight:300;color:var(--text)}

.company-card{left:73px;top:377px;width:190px}
.company-card h2{font-family:"Prata",serif;font-weight:400;font-size:15.5px;color:var(--ink);margin-bottom:16px}
.info-row{display:flex;gap:6px;font-size:8.5px;line-height:11px;color:var(--ink);margin-bottom:17px}
.info-row svg{flex:0 0 8px;margin-top:1px}

.contact-form{left:287px;top:391px;width:413px}
.field-grid{display:grid;grid-template-columns:repeat(3,1fr);gap:6px 8.5px}
.field{height:27px;border:1px solid var(--line);padding:0 8px;display:flex;align-items:center;font-size:7.2px;color:var(--muted)}
.field.message{grid-column:1/4;height:83px;align-items:flex-start;padding-top:6px}
.newsletter{display:flex;align-items:center;gap:8px;margin-top:9px;font-size:7.2px;color:var(--muted);padding-left:2px}
.check{width:10px;height:10px;border:1px solid var(--line);border-radius:1px}
.verify{margin-top:12px;margin-left:2px;width:116px;height:29px;border:1px solid #d6d6d6;border-radius:2px;background:#f9f9f9;display:flex;align-items:center;padding:0 6px;gap:5px;font-size:5px;color:var(--ink);box-shadow:0 0 2px rgba(0,0,0,.08)}
.verify .check{width:10px;height:10px;background:var(--white);border:1.5px solid #c1c1c1}
.verify .mark{margin-left:auto;width:11px;height:11px;background:#b9c7d8;border-radius:2px}
.send{margin-top:12px;margin-left:1px;width:66px;height:27px;background:var(--green);color:var(--white);font-size:7.5px;font-weight:600;display:flex;align-items:center;justify-content:center}

/* map */
.map{position:absolute;left:0;top:675px;width:772px;height:316px;background:linear-gradient(135deg,#eef0f2 0%,#e8ebee 55%,#dfe6f2 100%)}

/* footer */
.site-footer{position:absolute;left:0;top:991px;width:772px;height:209px;background:var(--footer);color:var(--footer-text)}
.footer-brand{position:absolute;left:72px;top:86px;display:flex;align-items:center;gap:6px;font-size:16px;color:var(--white)}
.footer-col{position:absolute;top:37px}
.footer-col h3{font-family:"Prata",serif;font-weight:400;font-size:11px;color:var(--white);margin-bottom:12px}
.footer-col li{list-style:none;font-size:8.3px;margin-bottom:9.3px}
.footer-contact{display:flex;gap:6px;font-size:8.3px;line-height:10px;margin-bottom:14px}
.social{display:flex;align-items:center;gap:6px;font-size:8.3px;margin-bottom:4px}
.social i{width:18px;height:18px;border-radius:50%;background:var(--white);display:block}
.copyright{position:absolute;left:0;right:0;top:166px;text-align:center;font-size:7.4px;color:var(--footer-text)}
.copyright b{color:var(--white);font-weight:400}
</style>
</head>
<body>

<header class="site-header">
  <a class="brand" href="#"><span class="brand-dot"></span>StayLuce</a>
  <div class="utility-bar">
    <span><svg width="8" height="8" viewBox="0 0 10 10" fill="none" stroke="#fff" stroke-width="1"><circle cx="5" cy="3.2" r="2.2"/><path d="M1 9.5c0-2.2 1.8-3.6 4-3.6s4 1.4 4 3.6"/></svg>LOGIN</span>
    <span><svg width="9" height="8" viewBox="0 0 10 9" fill="none" stroke="#fff" stroke-width="1"><path d="M5 8.3 1.2 4.5A2.2 2.2 0 0 1 5 1.8a2.2 2.2 0 0 1 3.8 2.7z"/></svg>WHISHLIST</span>
    <span>EN <svg width="5" height="4" viewBox="0 0 6 4" fill="none" stroke="#fff"><path d="M1 1l2 2 2-2"/></svg></span>
  </div>
  <nav class="main-nav">
    <a href="#">HOME</a><a href="#">SEARCH</a><a href="#">PROPERTY</a><a href="#">CUSTOM</a><a class="active" href="#">CONTACT US</a>
  </nav>
</header>

<section class="hero" role="img" aria-label="Photo of an arcaded shopping street with lanterns, hanging flowers and a small canal bridge">
  <h1>CONTACT US</h1>
</section>

<div class="abs breadcrumb">Home &nbsp;/&nbsp; <b>Contact Us</b></div>
<h1 class="abs page-title">Contact Us</h1>
<p class="abs page-intro">Use this form to contact us regarding any topics other than specific property requests which should be done using the form on the property detail pages.</p>

<aside class="abs company-card">
  <h2>Stayluce</h2>
  <div class="info-row"><svg width="8" height="10" viewBox="0 0 8 10"><path d="M4 0a3.5 3.5 0 0 0-3.5 3.5C.5 6 4 10 4 10s3.5-4 3.5-6.5A3.5 3.5 0 0 0 4 0z" fill="#13b584"/><circle cx="4" cy="3.5" r="1.3" fill="#fff"/></svg><span>Via dei Pini 24 50100 Borgo Alto<br>Borgo Alto, Italy</span></div>
  <div class="info-row"><svg width="8" height="10" viewBox="0 0 8 10"><path d="M1.5.5h2l.6 2.4-1.3.8a5 5 0 0 0 2.5 3l1-1.2 2 .8v2.2C4 8.5.3 5 .5 1.5z" fill="#13b584"/></svg><span>Phone: +39 055 0100200</span></div>
  <div class="info-row"><svg width="9" height="10" viewBox="0 0 9 10"><rect x="0" y="2" width="9" height="8" fill="#13b584"/><rect x="2" y="0" width="5" height="3" fill="#13b584"/><rect x="1.5" y="4" width="2" height="5" fill="#fff"/><rect x="5" y="4" width="3" height="1" fill="#fff"/><rect x="5" y="6" width="3" height="1" fill="#fff"/></svg><span>Fax: +39 055 0100300</span></div>
  <div class="info-row"><svg width="9" height="9" viewBox="0 0 10 10"><path d="M5 0l1.2 2 2.3-.6-.6 2.3L10 5l-2.1 1.2.6 2.3-2.3-.6L5 10 3.8 7.9l-2.3.6.6-2.3L0 5l2.1-1.3-.6-2.3 2.3.6z" fill="#13b584"/></svg><span>VAT Code: IT00012345670</span></div>
</aside>

<form class="abs contact-form">
  <div class="field-grid">
    <div class="field">First Name:</div>
    <div class="field">Last Name:</div>
    <div class="field">Country:</div>
    <div class="field">Email:</div>
    <div class="field">Confirm Email:</div>
    <div class="field">Phone:</div>
    <div class="field message">Message:</div>
  </div>
  <div class="newsletter"><span class="check"></span>I would like to subscribe to your newsletter.</div>
  <div class="verify"><span class="check"></span>I'm not a robot<span class="mark"></span></div>
  <div class="send">SEND</div>
</form>

<section class="map" role="img" aria-label="Street map of the office surroundings with a location marker"></section>

<footer class="site-footer">
  <div class="footer-brand"><span class="brand-dot"></span>StayLuce</div>

  <div class="footer-col" style="left:216px">
    <h3>Quick Links</h3>
    <ul><li>Home</li><li>Search</li><li>Property</li><li>Custom</li><li>Contact Us</li></ul>
  </div>
  <div class="footer-col" style="left:338px">
    <h3>Company</h3>
    <ul><li>Privacy Policies</li><li>Reservation Policies</li><li>Cookie Policy</li></ul>
  </div>
  <div class="footer-col" style="left:467px">
    <h3>Contact Us</h3>
    <div class="footer-contact"><svg width="7" height="9" viewBox="0 0 8 10"><path d="M4 0a3.5 3.5 0 0 0-3.5 3.5C.5 6 4 10 4 10s3.5-4 3.5-6.5A3.5 3.5 0 0 0 4 0z" fill="#fff"/><circle cx="4" cy="3.5" r="1.3" fill="#1d1d1d"/></svg><span>Via dei Pini 24 50100<br>Borgo Alto (Italy)</span></div>
    <div class="footer-contact"><svg width="7" height="9" viewBox="0 0 8 10"><path d="M1.5.5h2l.6 2.4-1.3.8a5 5 0 0 0 2.5 3l1-1.2 2 .8v2.2C4 8.5.3 5 .5 1.5z" fill="#fff"/></svg><span>+39 055 0100200</span></div>
    <div class="footer-contact"><svg width="9" height="7" viewBox="0 0 10 7"><rect width="10" height="7" fill="#fff"/><path d="M0 0l5 4 5-4" fill="none" stroke="#1d1d1d"/></svg><span>info@stayluce.example</span></div>
  </div>
  <div class="footer-col" style="left:638px">
    <h3>Follow Us</h3>
    <div class="social"><i></i>Community</div>
    <div class="social"><i></i>Newsfeed</div>
    <div class="social"><i></i>Gallery</div>
  </div>

  <p class="copyright">Copyright © 2021 <b>StayLuce</b>. All rights reserved.</p>
</footer>

</body>
</html>
```